I am a general contractor in Portland, Or. I would like a clean and simple design layout, maybe using the "didot" font, blue and dark bronze in colors are preferred. On one side of the card, it would be nice to have a logo(attached photo) and business name(KTW Construction). I don't need my job title on the card, just some thing along the lines of "gordon pike, general contractor". Thanks much.

Target Market(s)

Adults from 30-55 years old. Middle to upper class.

Industry/Entity Type

Contractor

Contact Information for Business Card

KTW Construction
Gordon L. Pike
2843 NE 71st Ave.
Portland, Or. 97288
541.555.0187

Font styles to use
Other font styles liked:
• didot

Colors
3277b5
7f7f7f

Requirements
Should not have
• Too much going on.

```html
<!DOCTYPE html>
<html lang="en">
<head>
<meta charset="utf-8">
<title>KTW Construction – Business Card</title>
<link rel="stylesheet" href="https://fonts.googleapis.com/css2?family=Exo+2:wght@700&family=Michroma&display=swap">
<style>
  :root {
    --page: #e9eaec;
    --navy: #1f2d78;
    --band-top: #2f47a0;
    --band-bottom: #23337f;
    --silver: #9a9a9c;
    --paper-light: #ffffff;
    --paper-shade: #e3e3e5;
    --ink: #3a3a3c;
    --ink-soft: #7f7f7f;
    --sky: #1a8fd6;
    --sky-deep: #0c57a3;
    --white: #ffffff;
  }
  * { margin: 0; padding: 0; box-sizing: border-box; }
  html, body { width: 1200px; height: 900px; overflow: hidden; background: var(--page); }
  .canvas {
    width: 1200px; height: 900px;
    display: flex; flex-direction: column; align-items: center; justify-content: center; gap: 40px;
  }
  .card {
    position: relative; width: 660px; height: 380px; border-radius: 34px; overflow: hidden;
    box-shadow: 0 10px 28px rgba(0,0,0,.18);
  }
  /* front */
  .card-front { background: linear-gradient(160deg, var(--paper-light) 30%, var(--paper-shade) 100%); }
  .card-front .wave { position: absolute; inset: 0; }
  .brand {
    position: absolute; left: 44px; top: 40px; display: flex; align-items: center; gap: 16px;
  }
  .brand-dot { width: 46px; height: 46px; border-radius: 50%; background: var(--navy); }
  .brand-name {
    font-family: "Exo 2", sans-serif; font-weight: 700; font-size: 42px; line-height: 1;
    color: var(--navy);
  }
  .holder { position: absolute; left: 44px; top: 128px; font-family: "Michroma", sans-serif; }
  .holder-name { font-size: 19px; line-height: 26px; letter-spacing: 3px; font-variant: small-caps; color: var(--ink); }
  .holder-role { margin-top: 2px; font-size: 14px; line-height: 20px; letter-spacing: 3px; font-variant: small-caps; color: var(--ink-soft); }
  .contact {
    position: absolute; left: 420px; top: 276px; list-style: none;
    font-family: "Michroma", sans-serif; font-size: 10px; letter-spacing: 1px; color: var(--white);
  }
  .contact li { display: flex; align-items: center; gap: 8px; height: 13px; line-height: 13px; white-space: nowrap; }
  .contact li.continued { padding-left: 19px; }
  .contact svg { width: 11px; height: 11px; flex: none; }
  /* back */
  .card-back {
    background: radial-gradient(circle at 35% 30%, var(--sky) 0%, var(--sky-deep) 95%);
    display: flex; align-items: center; justify-content: center; gap: 20px;
  }
  .card-back .brand-dot { width: 60px; height: 60px; background: var(--white); }
  .card-back .brand-name { font-size: 54px; color: var(--white); }
</style>
</head>
<body>
<main class="canvas">
  <section class="card card-front" aria-label="Card front">
    <svg class="wave" viewBox="0 0 660 380" preserveAspectRatio="none" aria-hidden="true">
      <defs>
        <linearGradient id="band" x1="0" y1="0" x2="0" y2="1">
          <stop offset="0" stop-color="var(--band-top)"/>
          <stop offset="1" stop-color="var(--band-bottom)"/>
        </linearGradient>
      </defs>
      <path d="M0,192 C190,304 470,286 660,136" fill="none" stroke="var(--silver)" stroke-width="9"/>
      <path d="M0,208 C190,320 470,302 660,152 L660,380 L0,380 Z" fill="url(#band)"/>
    </svg>

    <div class="brand">
      <span class="brand-dot"></span>
      <span class="brand-name">KTW Construction</span>
    </div>

    <div class="holder">
      <p class="holder-name">Gordon Pike</p>
      <p class="holder-role">General Contractor</p>
    </div>

    <ul class="contact">
      <li><svg viewBox="0 0 12 12"><circle cx="6" cy="6" r="6" fill="#fff"/><path d="M6 2.5a2 2 0 0 0-2 2c0 1.6 2 4.5 2 4.5s2-2.9 2-4.5a2 2 0 0 0-2-2z" fill="#23337f"/></svg>2843 NE 71st Ave.,</li>
      <li class="continued">Portland, OR 97288</li>
      <li><svg viewBox="0 0 12 12"><circle cx="6" cy="6" r="6" fill="#fff"/><path d="M4 3l1.3 1.6-.7.9c.5 1 1.1 1.6 2 2l.9-.7L9 8l-.8 1C5.8 8.8 3.2 6.2 3 3.8z" fill="#23337f"/></svg>541-555-0187</li>
      <li><svg viewBox="0 0 12 12"><circle cx="6" cy="6" r="6" fill="#fff"/><rect x="4.2" y="2.6" width="3.6" height="6.8" rx=".7" fill="#23337f"/></svg>541-555-0142</li>
      <li><svg viewBox="0 0 12 12"><circle cx="6" cy="6" r="6" fill="#fff"/><rect x="3" y="4.5" width="6" height="4" rx=".5" fill="#23337f"/><rect x="4" y="3" width="4" height="2" fill="#23337f"/></svg>541-555-0163</li>
      <li><svg viewBox="0 0 12 12"><circle cx="6" cy="6" r="6" fill="#fff"/><rect x="3" y="3.8" width="6" height="4.4" fill="#23337f"/><path d="M3 3.8l3 2.4 3-2.4" stroke="#fff" stroke-width=".7" fill="none"/></svg>gordon@ktwbuild.com</li>
      <li><svg viewBox="0 0 12 12"><circle cx="6" cy="6" r="6" fill="#fff"/><circle cx="6" cy="6" r="3" fill="none" stroke="#23337f" stroke-width=".9"/><path d="M3 6h6M6 3v6" stroke="#23337f" stroke-width=".7"/></svg>www.ktwbuild.com</li>
    </ul>
  </section>

  <section class="card card-back" aria-label="Card back">
    <span class="brand-dot"></span>
    <span class="brand-name">KTW Construction</span>
  </section>
</main>
</body>
</html>
```